Ridgeline Journeys business card

please see website
www.ridgelinejourneys.comau

info needed on card
Curtis Halvey
Ph
email
Adventure Riding GPS trails

please use my logo and colours off my site

Curtis Halvey
curtis@ridgelinejourneys.com

```html
<!DOCTYPE html>
<html lang="en">
<head>
<meta charset="utf-8">
<title>Ridgeline Journeys – Business Card</title>
<link rel="stylesheet" href="https://fonts.googleapis.com/css2?family=Oswald:wght@700&family=Open+Sans:wght@300;400;600&display=swap">
<style>
  :root {
    --page: #e9e7e3;
    --card: #ffffff;
    --ink: #1e1e1e;
    --muted: #3a3a3a;
    --band: #8a8a8a;
    --band-dark: #6e6e6e;
    --accent: #e9df2a;
    --mark: #9a9a9a;
  }
  * { box-sizing: border-box; margin: 0; padding: 0; }
  html, body { width: 1200px; height: 892px; overflow: hidden; }
  body {
    background: var(--page);
    display: flex; flex-direction: column; align-items: center; justify-content: center;
    gap: 36px;
    font-family: "Open Sans", Arial, sans-serif;
    color: var(--ink);
  }
  .card {
    position: relative;
    width: 700px; height: 400px;
    background: var(--card);
    box-shadow: 0 6px 18px rgba(0,0,0,.18);
    overflow: hidden;
  }
  .stripe-line { position: absolute; left: 0; right: 0; height: 7px; background: var(--accent); }
  .stripe-band { position: absolute; left: 0; right: 0; height: 66px; background: linear-gradient(var(--band), var(--band-dark)); }
  .card--front .stripe-line { bottom: 80px; }
  .card--front .stripe-band { bottom: 0; }
  .card--back .stripe-line { top: 80px; }
  .card--back .stripe-band { top: 0; }

  .brand-dot {
    position: absolute; width: 120px; height: 120px; border-radius: 50%;
    background: var(--mark);
  }
  .wordmark {
    position: absolute;
    font-family: "Oswald", Impact, sans-serif; font-weight: 700;
    color: var(--ink); text-transform: uppercase; line-height: .98;
    letter-spacing: 1px;
  }
  .wordmark span { display: block; }

  .card--front .brand-dot { left: 56px; top: 44px; }
  .card--front .wordmark { left: 214px; top: 44px; }
  .card--front .wordmark .w1 { font-size: 46px; }
  .card--front .wordmark .w2 { font-size: 62px; }

  .person {
    position: absolute; left: 56px; top: 210px;
    font-weight: 300; font-size: 30px; color: var(--muted);
  }
  .divider { position: absolute; left: 290px; top: 190px; width: 1.5px; height: 86px; background: var(--muted); }
  .contact { position: absolute; left: 310px; top: 200px; list-style: none; }
  .contact li { display: flex; align-items: center; gap: 8px; font-size: 20px; line-height: 32px; color: var(--ink); }
  .contact svg { width: 16px; height: 16px; flex: none; }

  .card--back .brand-dot { left: 290px; top: 120px; }
  .card--back .wordmark { left: 0; right: 0; top: 260px; text-align: center; }
  .card--back .wordmark .w1 { font-size: 40px; }
  .card--back .wordmark .w2 { font-size: 54px; }
</style>
</head>
<body>
  <section class="card card--front">
    <div class="brand-dot"></div>
    <h1 class="wordmark"><span class="w1">Ridgeline</span><span class="w2">Journeys</span></h1>
    <p class="person">Curtis Halvey</p>
    <div class="divider"></div>
    <ul class="contact">
      <li>
        <svg viewBox="0 0 16 16" aria-hidden="true"><rect width="16" height="16" fill="#1e1e1e"/><path d="M3 5h10v7H3z M3 5l5 4 5-4" fill="none" stroke="#fff" stroke-width="1.3"/></svg>
        curtis@ridgelinejourneys.com
      </li>
      <li>
        <svg viewBox="0 0 16 16" aria-hidden="true"><rect width="16" height="16" fill="#1e1e1e"/><circle cx="8" cy="8" r="4.5" fill="none" stroke="#fff" stroke-width="1.3"/><path d="M3.5 8h9M8 3.5v9" stroke="#fff" stroke-width="1"/></svg>
        www.ridgelinejourneys.com.au
      </li>
    </ul>
    <div class="stripe-line"></div>
    <div class="stripe-band"></div>
  </section>

  <section class="card card--back">
    <div class="stripe-band"></div>
    <div class="stripe-line"></div>
    <div class="brand-dot"></div>
    <h2 class="wordmark"><span class="w1">Ridgeline</span><span class="w2">Journeys</span></h2>
  </section>
</body>
</html>
```